Corporate Business Card

Very professional, Modern, Not to busy, include phone address email, website
(253) 617-4930, 18761 52nd Avenue S, Kent, WA 98047, martin@plumlinegroup.com, varkoworks.com

Target Market(s)

Manufacturing

Industry/Entity Type

Aero, machining, manufacturing, Off road racing

Contact Information for Business Card

Phone, address email, website

```html
<!DOCTYPE html>
<html lang="en">
<head>
<meta charset="UTF-8">
<title>Varko Works — Business Card</title>
<link rel="stylesheet" href="https://fonts.googleapis.com/css2?family=Montserrat:wght@500;600;800&display=swap">
<style>
  :root {
    --brand-red: #d42129;
    --brand-navy: #1b3a78;
    --ink: #1e1e1e;
    --paper: #ffffff;
    --backdrop: #e6e6e6;
  }
  * { box-sizing: border-box; margin: 0; padding: 0; }
  html, body {
    width: 1200px; height: 900px; overflow: hidden;
    background: var(--backdrop);
    font-family: "Montserrat", sans-serif;
  }
  .sheet { position: relative; width: 1200px; height: 900px; }
  .card {
    position: absolute; left: 268px;
    width: 665px; height: 380px;
    box-shadow: 0 6px 18px rgba(0,0,0,.18);
    overflow: hidden;
  }
  .card--front { top: 50px; background: var(--brand-red); }
  .card--back { top: 470px; background: var(--paper); }

  .wordmark {
    position: absolute; display: flex; align-items: center; gap: 14px;
    font-weight: 800; letter-spacing: 1px; text-transform: uppercase;
  }
  .wordmark__square { width: 18px; height: 18px; }
  .card--front .wordmark {
    left: 0; right: 0; top: 150px; justify-content: center;
    color: var(--paper); font-size: 60px;
  }
  .card--front .wordmark__square { background: var(--paper); width: 26px; height: 26px; }
  .card--back .wordmark {
    right: 44px; top: 46px; color: var(--brand-navy); font-size: 40px;
  }
  .card--back .wordmark__square { background: var(--brand-red); }

  .wave { position: absolute; inset: 0; width: 665px; height: 380px; }

  .address {
    position: absolute; left: 46px; top: 138px;
    color: var(--ink); font-size: 17px; font-weight: 500; line-height: 1.4;
    font-style: normal;
  }
  .contacts {
    position: absolute; left: 46px; top: 204px; list-style: none;
    color: var(--ink); font-size: 16px; font-weight: 500;
  }
  .contacts__item { display: flex; align-items: center; gap: 10px; height: 26px; }
  .contacts__icon { width: 16px; height: 16px; flex: none; }
</style>
</head>
<body>
<main class="sheet">
  <section class="card card--front" aria-label="Card front">
    <div class="wordmark"><span class="wordmark__square"></span>Varko Works</div>
  </section>

  <section class="card card--back" aria-label="Card back">
    <svg class="wave" viewBox="0 0 665 380" aria-hidden="true">
      <path d="M0 330 C 330 336, 480 222, 665 108 L665 380 L0 380 Z" fill="var(--brand-navy)"/>
      <path d="M0 343 C 330 348, 480 234, 665 114 L665 380 L0 380 Z" fill="var(--paper)"/>
      <path d="M0 352 C 330 357, 480 244, 665 120 L665 380 L0 380 Z" fill="var(--brand-red)"/>
    </svg>

    <div class="wordmark"><span class="wordmark__square"></span>Varko Works</div>

    <address class="address">
      18761 52nd Avenue S,<br>Kent, WA 98047
    </address>

    <ul class="contacts">
      <li class="contacts__item">
        <svg class="contacts__icon" viewBox="0 0 16 16" aria-hidden="true">
          <path d="M3 1h3l1.5 4-2 1.2a9 9 0 0 0 4.3 4.3L11 8.5l4 1.5v3a2 2 0 0 1-2 2A13 13 0 0 1 1 3a2 2 0 0 1 2-2z" fill="var(--brand-red)"/>
        </svg>
        (253) 617-4930
      </li>
      <li class="contacts__item">
        <svg class="contacts__icon" viewBox="0 0 16 16" aria-hidden="true">
          <rect x="1" y="3" width="14" height="10" rx="1" fill="var(--brand-red)"/>
          <path d="M1.5 3.8 8 9l6.5-5.2" fill="none" stroke="var(--paper)" stroke-width="1.3"/>
        </svg>
        martin@plumlinegroup.com
      </li>
      <li class="contacts__item">
        <svg class="contacts__icon" viewBox="0 0 16 16" aria-hidden="true">
          <circle cx="8" cy="8" r="7" fill="var(--brand-red)"/>
          <path d="M1 8h14M8 1c-3 3.5-3 10.5 0 14M8 1c3 3.5 3 10.5 0 14" fill="none" stroke="var(--paper)" stroke-width="1"/>
        </svg>
        www.varkoworks.com
      </li>
    </ul>
  </section>
</main>
</body>
</html>
```